Agriculture Business Card

I want to use my existing logo and use my tagline of "Don't Guess...Soil Test" on the card. Looking for a double sided card that will really get peoples attention.
Contact Info:
Marlow Field Crop Edge
Calvin Brusk
2917 K Lane
Larkin, NE 68593
402-555-0193
calvin.r.brusk@fieldmailbox.net

```html
<!DOCTYPE html>
<html lang="en">
<head>
<meta charset="utf-8">
<title>Marlow Field Crop Edge – Business Card</title>
<link href="https://fonts.googleapis.com/css2?family=Poppins:wght@400;500;600&family=Oswald:wght@500;600&display=swap" rel="stylesheet">
<style>
  :root {
    --backdrop: #1d1d1f;
    --card-white: #ffffff;
    --card-black: #111113;
    --pattern-dark: #1a1a1c;
    --pattern-mid: #3a3b3e;
    --pattern-light: #74757a;
    --brand-brown: #8a5a44;
    --text-brown: #5a3a2a;
    --brand-green: #3aaa35;
    --brand-orange: #f5ae1a;
    --rule-green: #7cc36a;
  }
  * { box-sizing: border-box; margin: 0; padding: 0; }
  html, body { width: 1200px; height: 1108px; overflow: hidden; }
  body {
    background: var(--backdrop);
    font-family: "Poppins", sans-serif;
    display: flex;
    align-items: center;
    justify-content: center;
    gap: 60px;
  }
  .card {
    width: 420px;
    height: 735px;
    border-radius: 22px;
    position: relative;
    overflow: hidden;
  }

  /* Front */
  .card-front {
    background: var(--card-white);
    display: flex;
    flex-direction: column;
    align-items: center;
    padding: 80px 30px 0;
    text-align: center;
  }
  .brand {
    display: flex;
    flex-direction: column;
    align-items: center;
    gap: 26px;
  }
  .brand-disc {
    width: 190px;
    height: 190px;
    border-radius: 50%;
    background: var(--brand-orange);
  }
  .brand-name {
    font-family: "Oswald", sans-serif;
    font-weight: 500;
    font-size: 46px;
    line-height: 1.05;
    color: var(--brand-brown);
  }
  .contact { margin-top: 46px; width: 100%; }
  .person-name {
    font-weight: 600;
    font-size: 28px;
    letter-spacing: .5px;
    color: var(--brand-green);
    text-transform: uppercase;
  }
  .rule {
    width: 170px;
    height: 1px;
    background: var(--rule-green);
    margin: 8px auto 10px;
  }
  .contact-line {
    font-size: 18px;
    color: var(--text-brown);
    line-height: 1.45;
  }
  .company-line { color: var(--brand-orange); }

  /* Back */
  .card-back { background: var(--card-black); }
  .pattern {
    position: absolute;
    inset: 0;
    background:
      linear-gradient(215deg, var(--pattern-light) 0%, var(--pattern-mid) 35%, var(--pattern-dark) 70%, #000 100%);
  }
  .back-mark {
    position: absolute;
    left: 0;
    right: 0;
    top: 430px;
    display: flex;
    align-items: center;
    justify-content: center;
    gap: 10px;
  }
  .back-mark-disc {
    width: 46px;
    height: 46px;
    border-radius: 50%;
    background: var(--brand-green);
  }
  .back-mark-name {
    font-weight: 600;
    font-size: 17px;
    color: var(--brand-orange);
  }
  .tagline {
    position: absolute;
    left: 0;
    right: 0;
    top: 505px;
    text-align: center;
    font-family: "Oswald", sans-serif;
    font-weight: 500;
    font-size: 36px;
    color: var(--brand-orange);
    text-transform: uppercase;
  }
</style>
</head>
<body>
  <section class="card card-front">
    <div class="brand">
      <span class="brand-disc"></span>
      <span class="brand-name">Marlow Field<br>Crop Edge</span>
    </div>
    <div class="contact">
      <p class="person-name">Calvin Brusk</p>
      <div class="rule"></div>
      <p class="contact-line">402-555-0193</p>
      <p class="contact-line">calvin.r.brusk@fieldmailbox.net</p>
      <div class="rule"></div>
      <p class="contact-line company-line">Marlow Field Crop Edge</p>
      <p class="contact-line">2917 K Lane, Larkin, NE 68593</p>
    </div>
  </section>

  <section class="card card-back">
    <div class="pattern" role="img" aria-label="Repeating tonal grey pattern of the brand symbol, lighter toward the top right"></div>
    <div class="back-mark">
      <span class="back-mark-disc"></span>
      <span class="back-mark-name">Marlow Field Crop Edge</span>
    </div>
    <p class="tagline">Don't Guess...Soil Test</p>
  </section>
</body>
</html>
```